Business Broker Graphics Package

Hi,

Seeking a smart and professional graphics package design including business card design (double-sided) and letterhead and PowerPoint slide template.

3 Deliverables:

1. Company Letterhead
2. Business Card (two sided) (will consider one sided designs)
3. PowerPoint Template. Requires cover PPT and 2nd page design.

For the prototype use this info:
Marcus Dellorane RPA
Registered Practice Adviser
5678 Harlow Rd.
Tampa, FL 77777
555.014.2273
Demo@Quillbrookpath.com
www.QuillbrookPath.com

I'll give exact information to winner to finalize later.

I've attached the logo..

Business card will be double sided and info for back of card is in attachment.

Look forward to your great ideas and concepts!

Target Market(s)

President's and business owners, CPA's and other professionals.

Industry/Entity Type

Business

Requirements
Nice to have
• Prefer horizontal card, but will consider vertical card design.

The business card should be all or primarily white. Text colors should be same as logo creative combination of black and forest green.

PowerPoint can be white background or lighter palette of colors I like gold color. I do not like darkly colored PowerPoint designs I prefer light and bright designs.

```html
<!DOCTYPE html>
<html lang="en">
<head>
<meta charset="utf-8">
<title>Quillbrook Path – Stationery Package</title>
<link rel="stylesheet" href="https://fonts.googleapis.com/css2?family=Open+Sans:wght@400;700&family=Arimo:wght@400;700&display=swap">
<style>
  :root {
    --backdrop: #9b9b9b;
    --paper: #ffffff;
    --forest: #0f4a2a;
    --gold: #e6c21e;
    --gold-soft: #eed35e;
    --ink: #161616;
    --muted: #555555;
    --rule: #dcdcdc;
    --skyline-soft: #ececec;
  }
  * { box-sizing: border-box; margin: 0; padding: 0; }
  html, body { width: 1200px; height: 640px; overflow: hidden; }
  body { background: var(--backdrop); position: relative; font-family: "Open Sans", Arial, sans-serif; color: var(--ink); }

  .sheet { position: absolute; background: var(--paper); box-shadow: 3px 4px 6px rgba(0,0,0,.35); overflow: hidden; }

  /* company name set as plain text */
  .company-name { position: absolute; font-family: "Open Sans", Arial, sans-serif; font-weight: 700; color: var(--forest); line-height: 1; white-space: nowrap; }

  /* soft placeholder where the skyline decoration sits */
  .skyline-area { position: absolute; background: linear-gradient(180deg, rgba(220,220,220,0) 0%, var(--skyline-soft) 100%); }
  .footer-line { position: absolute; left: 0; right: 0; height: 2px; background: var(--rule); }
  .contact-foot { position: absolute; font-size: 5.2px; color: var(--ink); white-space: nowrap; }
  .contact-foot span + span { border-left: 1px solid var(--muted); padding-left: 3px; margin-left: 3px; }

  .service-list { list-style: none; display: flex; justify-content: center; gap: 5px; font-family: "Arimo", Arial, sans-serif; color: var(--forest); white-space: nowrap; }
  .service-list li::before { content: ""; display: inline-block; width: 3px; height: 3px; background: currentColor; margin-right: 2px; vertical-align: middle; }
  .slogan { font-family: "Arimo", Arial, sans-serif; font-weight: 700; text-transform: uppercase; letter-spacing: .08em; }

  /* letterhead */
  .letterhead { left: 14px; top: 30px; width: 400px; height: 516px; }
  .letterhead .company-name { top: 68px; left: 0; right: 0; text-align: center; font-size: 15px; }
  .letter { position: absolute; left: 36px; right: 30px; top: 118px; font-size: 5.3px; line-height: 11.6px; }
  .letter__name { font-weight: 700; }
  .letter__body { margin-top: 14px; }
  .letter__body p { margin-bottom: 11.6px; }
  .signature { width: 72px; height: 22px; margin-top: 2px; background: linear-gradient(90deg, #2a2a2a22, #2a2a2a55, #2a2a2a22); border-radius: 3px; }
  .letter__sign-name { font-weight: 700; margin-top: 4px; }
  .letterhead .skyline-area { left: 196px; right: 0; top: 456px; height: 66px; }
  .letterhead .footer-line { bottom: 22px; }
  .letterhead .contact-foot { left: 36px; bottom: 29px; }

  /* gold cover slide */
  .slide-cover { left: 430px; top: 34px; width: 370px; height: 276px; background: var(--gold); }
  .slide-cover svg { position: absolute; left: 0; top: 0; }
  .slide-cover .skyline-area { left: 242px; right: 0; top: 4px; height: 42px; background: linear-gradient(180deg, rgba(238,211,94,0) 0%, var(--gold-soft) 100%); }
  .slide-cover .company-name { top: 238px; left: 0; right: 0; text-align: center; font-size: 12px; }
  .slide-cover .service-list { position: absolute; left: 0; right: 0; top: 258px; font-size: 6.4px; }

  /* white content slide */
  .slide-content { left: 814px; top: 34px; width: 370px; height: 275px; }
  .slide-content .company-name { top: 34px; left: 17px; font-size: 8px; }
  .slide-content .skyline-area { left: 258px; right: 0; top: 240px; height: 27px; }
  .slide-content .footer-line { bottom: 8px; }
  .slide-content .contact-foot { left: 17px; top: 254px; font-size: 4.8px; }

  /* business card front */
  .card-front { left: 526px; top: 368px; width: 258px; height: 150px; }
  .card-front .company-name { top: 42px; left: 17px; font-size: 10.5px; }
  .holder { position: absolute; right: 16px; top: 49px; text-align: right; font-family: "Arimo", Arial, sans-serif; }
  .holder__name { font-size: 10px; color: #333; }
  .holder__title { font-size: 5.4px; margin-top: 4px; padding-top: 3px; border-top: 1px solid var(--rule); }
  .contact-list { position: absolute; left: 16px; top: 79px; list-style: none; font-family: "Arimo", Arial, sans-serif; font-size: 6.6px; color: #333; }
  .contact-list li { display: flex; align-items: center; gap: 4px; height: 11px; white-space: nowrap; }
  .contact-list svg { width: 8px; height: 8px; flex: none; }
  .card-front .skyline-area { left: 114px; right: 0; top: 84px; height: 44px; }
  .card-front .footer-line { top: 128px; height: 1.5px; }
  .card-front .slogan { position: absolute; left: 16px; top: 136px; font-size: 6.2px; color: var(--forest); }

  /* business card back */
  .card-back { left: 814px; top: 368px; width: 256px; height: 148px; }
  .card-back .company-name { top: 58px; left: 0; right: 0; text-align: center; font-size: 15px; }
  .card-back__band { position: absolute; left: 0; right: 0; top: 96px; bottom: 0; background: var(--forest); color: #fff; text-align: center; }
  .card-back__band .slogan { font-size: 7px; margin-top: 10px; }
  .card-back__band .service-list { color: #fff; font-size: 6.2px; margin-top: 6px; }
</style>
</head>
<body>

  <section class="sheet letterhead" aria-label="Letterhead">
    <p class="company-name">Quillbrook Path</p>
    <div class="letter">
      <p>To</p>
      <p class="letter__name">The Lorem Ipsum</p>
      <p>Sample text for printing and typesetting industry</p>
      <div class="letter__body">
        <p>Lorem Ipsum is simply dummy text of the printing and typesetting industry. Lorem Ipsum has been the industry's standard dummy text ever since the 1500s, when an unknown printer took a galley of type and scrambled it to make a type specimen book. It has survived not only five centuries, but also the leap into electronic typesetting, remaining essentially unchanged. It was popularised in the 1960s with the release of Letraset sheets containing Lorem Ipsum passages, and more recently with desktop publishing software including versions of Lorem Ipsum.</p>
        <p>It is a long established fact that a reader will be distracted by the readable content of a page when looking at its layout. The point of using Lorem Ipsum is that it has a more-or-less normal distribution of letters, as opposed to using 'Content here, content here', making it look like readable English. Many desktop publishing packages and web page editors now use Lorem Ipsum as their default model text, and a search for 'lorem ipsum' will uncover many web sites still in their infancy. Various versions have evolved over the years, sometimes by accident, sometimes on purpose (injected humour and the It is a long established fact that a reader will be distracted by the readable content of a page when looking at its layout. The point of using Lorem Ipsum is that it has a more-or-less normal distribution of letters, as opposed to using 'Content here, content here', making it look like readable English. Many desktop publishing packages and web page editors now use Lorem Ipsum as their default model text, and a search for 'lorem ipsum' will uncover many web sites still in their infancy.</p>
        <p>It is a long established fact that a reader will be distracted by the readable content of a page when looking at its layout. The point of using Lorem Ipsum is that it has a more-or-less normal distribution of letters, as opposed to using 'Content here, content here', making it look like readable English. Many desktop publishing packages and web page editors now use Lorem Ipsum as their default model text, and a search for 'lorem ipsum' will uncover many web sites still in their infancy. Various versions have evolved over the years, sometimes by accident, sometimes on purpose.</p>
      </div>
      <div class="signature" role="img" aria-label="Handwritten signature"></div>
      <p class="letter__sign-name">The Lorem Ipsum</p>
      <p>Sample text for printing and typesetting industry</p>
    </div>
    <div class="skyline-area" role="img" aria-label="Faint city skyline decoration"></div>
    <p class="contact-foot"><span>555.014.2273</span><span>www.QuillbrookPath.com</span></p>
    <div class="footer-line"></div>
  </section>

  <section class="sheet slide-cover" aria-label="Presentation cover slide">
    <svg width="370" height="276" viewBox="0 0 370 276" aria-hidden="true">
      <line x1="0" y1="46" x2="370" y2="46" stroke="#ffffff" stroke-opacity=".55" stroke-width="1.5"/>
      <path d="M-4 280 Q185 100 374 280 Z" fill="#ffffff"/>
      <path d="M-4 280 Q185 100 374 280" fill="none" stroke="var(--forest)" stroke-width="6"/>
    </svg>
    <div class="skyline-area" role="img" aria-label="Faint city skyline decoration"></div>
    <p class="company-name">Quillbrook Path</p>
    <ul class="service-list">
      <li>Business Sale</li><li>Acquisition</li><li>Exit Planning</li><li>Valuation</li><li>Growth Engineering</li>
    </ul>
  </section>

  <section class="sheet slide-content" aria-label="Presentation content slide">
    <p class="company-name">Quillbrook Path</p>
    <div class="skyline-area" role="img" aria-label="Faint city skyline decoration"></div>
    <p class="contact-foot"><span>555.014.2273</span><span>www.QuillbrookPath.com</span></p>
    <div class="footer-line"></div>
  </section>

  <section class="sheet card-front" aria-label="Business card front">
    <p class="company-name">Quillbrook Path</p>
    <div class="holder">
      <p class="holder__name">Marcus Dellorane RPA</p>
      <p class="holder__title">Registered Practice Adviser</p>
    </div>
    <div class="skyline-area" role="img" aria-label="Faint city skyline decoration"></div>
    <ul class="contact-list">
      <li>
        <svg viewBox="0 0 8 8" aria-hidden="true"><rect width="8" height="8" rx="1" fill="var(--forest)"/><rect x="2.6" y="1.4" width="2.8" height="5.2" rx=".6" fill="#fff"/></svg>
        555.014.2273
      </li>
      <li>
        <svg viewBox="0 0 8 8" aria-hidden="true"><rect width="8" height="8" rx="1" fill="var(--forest)"/><path d="M4 7 L2.2 4.2 A2 2 0 1 1 5.8 4.2 Z" fill="#fff"/><circle cx="4" cy="3.2" r=".7" fill="var(--forest)"/></svg>
        5678 Harlow Rd. Tampa, FL 77777
      </li>
      <li>
        <svg viewBox="0 0 8 8" aria-hidden="true"><rect width="8" height="8" rx="1" fill="var(--forest)"/><rect x="1.5" y="2.4" width="5" height="3.4" fill="#fff"/><path d="M1.5 2.4 L4 4.3 L6.5 2.4" fill="none" stroke="var(--forest)" stroke-width=".5"/></svg>
        Demo@Quillbrookpath.com
      </li>
      <li>
        <svg viewBox="0 0 8 8" aria-hidden="true"><rect width="8" height="8" rx="1" fill="var(--forest)"/><circle cx="4" cy="4" r="2.5" fill="none" stroke="#fff" stroke-width=".6"/><line x1="1.5" y1="4" x2="6.5" y2="4" stroke="#fff" stroke-width=".5"/><ellipse cx="4" cy="4" rx="1" ry="2.5" fill="none" stroke="#fff" stroke-width=".5"/></svg>
        www.QuillbrookPath.com
      </li>
    </ul>
    <div class="footer-line"></div>
    <p class="slogan">Ownership Solutions</p>
  </section>

  <section class="sheet card-back" aria-label="Business card back">
    <p class="company-name">Quillbrook Path</p>
    <div class="card-back__band">
      <p class="slogan">Ownership Solutions</p>
      <ul class="service-list">
        <li>Business Sale</li><li>Acquisition</li><li>Exit Planning</li><li>Valuation</li><li>Growth Engineering</li>
      </ul>
    </div>
  </section>

</body>
</html>
```